Tall fern bicycle rental

would like to have a bicycle rental website that has the ability to have a calender and be able to sign a liability waiver and pay all on line, We rent fat tire vorn bicycles

```html
<!DOCTYPE html>
<html lang="en">
<head>
<meta charset="utf-8">
<title>Tall Fern Bicycle Rental</title>
<link href="https://fonts.googleapis.com/css2?family=Poppins:wght@400;500;600;700;800&family=Open+Sans:wght@400;600;700&display=swap" rel="stylesheet">
<style>
:root{
  --blue:#1e88d8;
  --blue-dark:#1565b0;
  --navy:#141e3c;
  --ink:#1a1a1a;
  --text:#3d3d3d;
  --footer:#2a2a2a;
  --footer-text:#d6d6d6;
  --white:#ffffff;
}
*{margin:0;padding:0;box-sizing:border-box}
html,body{width:1200px;height:3673px;overflow:hidden}
body{position:relative;background:var(--white);font-family:'Open Sans',Arial,sans-serif;color:var(--text)}
.abs{position:absolute}
.heading{font-family:'Poppins',Arial,sans-serif}
.rule{position:absolute;height:4px;width:42px;background:var(--blue)}
.btn{position:absolute;background:var(--blue);color:var(--white);font-family:'Poppins',Arial,sans-serif;font-weight:700;font-size:11px;letter-spacing:.3px;display:flex;align-items:center;justify-content:center;text-transform:uppercase}

/* hero */
.hero-photo{position:absolute;left:0;top:0;width:1200px;height:658px;background:linear-gradient(180deg,#c9d8e6 0%,#e8eef3 30%,#b7cbd9 52%,#5f7f6a 62%,#8a6a58 80%,#6d5547 100%)}
.brand{position:absolute;left:128px;top:40px;display:flex;align-items:center;gap:10px}
.brand-dot{width:44px;height:44px;border-radius:50%;background:var(--blue)}
.brand-name{font-family:'Poppins',Arial,sans-serif;font-weight:700;font-size:17px;line-height:1.1;color:var(--blue-dark);width:140px}
.follow-label{left:605px;top:29px;font-size:9px;font-weight:700;color:var(--ink)}
.social{position:absolute;width:26px;height:26px;border-radius:50%;background:var(--navy)}
.call-icon{left:794px;top:25px;width:26px;height:26px;border-radius:50%;background:var(--blue)}
.call-label{left:827px;top:20px;font-size:9px;font-weight:700;color:var(--ink)}
.call-number{left:826px;top:30px;font-family:'Poppins',Arial,sans-serif;font-size:20px;font-weight:500;color:var(--ink)}
.sign-in{left:989px;top:26px;width:83px;height:25px;font-size:12px;font-weight:500}
.nav{position:absolute;top:70px;left:0;width:1200px;font-family:'Poppins',Arial,sans-serif;font-size:13px;font-weight:500;color:var(--ink)}
.nav span{position:absolute;white-space:nowrap}
.nav .active{color:var(--blue);border-bottom:1.5px solid var(--blue)}
.hero-title{left:128px;top:200px;font-size:37px;color:var(--ink);line-height:46px}
.hero-title b{font-weight:800;display:block}
.hero-title span{font-weight:400}
.check-box{left:130px;top:319px;width:414px;height:60px;background:var(--white);box-shadow:0 2px 8px rgba(0,0,0,.1)}
.check-label{left:178px;top:342px;font-size:13px;font-weight:600;color:var(--ink)}
.check-btn{left:433px;top:329px;width:100px;height:40px;font-size:17px;font-weight:600}
.dot{position:absolute;top:620px;width:8px;height:8px;border-radius:50%;background:rgba(255,255,255,.8)}
.dot.on{background:var(--blue);border:2px solid #fff;width:11px;height:11px;top:619px}

/* section titles */
.section-title{position:absolute;left:0;width:1200px;text-align:center;font-family:'Poppins',Arial,sans-serif;font-weight:700;font-size:25px;color:var(--ink)}

/* pricing */
.price-card{position:absolute;top:799px;width:278px;height:320px;background:var(--white);box-shadow:0 3px 14px rgba(0,0,0,.14);text-align:center}
.price{margin-top:42px;font-family:'Poppins',Arial,sans-serif;font-weight:800;font-size:40px;color:var(--blue);line-height:44px}
.price sup{font-size:20px;vertical-align:14px}
.plan{font-family:'Poppins',Arial,sans-serif;font-weight:600;font-size:18px;color:var(--blue-dark);margin-top:4px}
.price-text{margin:24px auto 0;width:210px;font-size:13.5px;line-height:20px;color:var(--text)}
.price-card .btn{left:88px;top:248px;width:101px;height:29px}

/* welcome */
.welcome-photo{position:absolute;left:0;top:1180px;width:1200px;height:506px;background:linear-gradient(180deg,#9fb4c9 0%,#6a8a6a 25%,#3f6f7f 45%,#4f7f8f 65%,#7d6a5a 85%,#5e4d40 100%)}
.welcome-panel{left:158px;top:1228px;width:381px;height:411px;background:rgba(255,255,255,.94)}
.welcome-kicker{left:195px;top:1258px;font-family:'Poppins',Arial,sans-serif;font-size:18px;color:var(--ink)}
.welcome-name{left:195px;top:1285px;font-family:'Poppins',Arial,sans-serif;font-weight:700;font-size:21px;color:var(--ink)}
.welcome-text{left:195px;top:1353px;width:310px;font-size:15px;line-height:21px;color:var(--text)}

/* how it works */
.step-photo{position:absolute;top:1840px;width:296px;height:205px}
.step-title{position:absolute;top:2068px;font-family:'Poppins',Arial,sans-serif;font-weight:700;font-size:20px;color:var(--ink)}
.step-text{position:absolute;top:2107px;width:290px;font-size:13px;line-height:17.5px;color:var(--text)}

/* fat tire */
.fat-photo{position:absolute;left:0;top:2243px;width:1200px;height:513px;background:linear-gradient(90deg,#e9eef2 0%,#dfe7ea 35%,#a8bba0 60%,#c3d2c8 80%,#9fb29a 100%)}
.fat-title{left:164px;top:2335px;font-family:'Poppins',Arial,sans-serif;font-weight:800;font-size:33px;line-height:37px;color:var(--ink)}
.fat-text{left:164px;top:2462px;width:320px;font-size:17.5px;line-height:22.5px;color:var(--ink)}

/* testimonials */
.testi-band{position:absolute;left:0;top:2756px;width:1200px;height:448px;background:var(--blue)}
.testi-card{position:absolute;top:2910px;width:298px;height:275px;background:var(--white)}
.quote{position:absolute;left:14px;top:4px;font-family:'Poppins',Arial,sans-serif;font-weight:800;font-size:44px;color:var(--blue)}
.stars{position:absolute;left:40px;top:52px;font-size:12px;letter-spacing:2px;color:var(--blue)}
.testi-text{position:absolute;left:40px;top:78px;width:230px;font-size:12.5px;line-height:17.5px;color:var(--text)}
.testi-rule{position:absolute;left:42px;top:226px;width:30px;height:2px;background:var(--blue)}
.testi-name{position:absolute;left:42px;top:236px;font-size:12px;font-weight:700;color:var(--blue-dark)}

/* footer */
.footer{position:absolute;left:0;top:3204px;width:1200px;height:469px;background:var(--footer)}
.foot-dot{left:163px;top:3305px;width:160px;height:160px;border-radius:50%;background:var(--blue)}
.foot-brand{left:133px;top:3480px;width:220px;text-align:center;font-family:'Poppins',Arial,sans-serif;font-weight:600;font-size:16px;color:var(--white)}
.foot-head{position:absolute;top:3311px;font-family:'Poppins',Arial,sans-serif;font-weight:700;font-size:15px;color:var(--white);letter-spacing:.4px}
.foot-menu{left:446px;top:3352px;font-size:13.5px;line-height:24px;color:var(--footer-text)}
.foot-icon{position:absolute;width:28px;height:28px;border-radius:50%;background:var(--white)}
.foot-line{position:absolute;font-size:13.5px;line-height:19px;color:var(--footer-text)}
.foot-rule{left:125px;top:3573px;width:941px;height:1px;background:#4a4a4a}
.copyright{left:0;top:3607px;width:1200px;text-align:center;font-size:11.5px;color:var(--footer-text)}
</style>
</head>
<body>

<!-- hero -->
<div class="hero-photo" role="img" aria-label="Couple riding bicycles along a lakeside brick path under a bright sky"></div>
<div class="brand"><div class="brand-dot"></div><div class="brand-name">Tall Fern Bicycle Rental</div></div>
<div class="abs follow-label">FOLLOW US</div>
<div class="social" style="left:677px;top:22px"></div>
<div class="social" style="left:711px;top:22px"></div>
<div class="social" style="left:745px;top:22px"></div>
<div class="abs call-icon">
  <svg width="26" height="26" viewBox="0 0 26 26"><path d="M9 7c1 0 2 2.5 2 3s-1 1-1 1.5c0 1 3 4 4 4 .5 0 1-1 1.5-1s3 1 3 2-1 2.5-2.5 2.5C11 19 7 15 7 9.5 7 8 8 7 9 7z" fill="#fff"/></svg>
</div>
<div class="abs call-label">CALL US</div>
<div class="abs call-number">888.888.8888</div>
<div class="btn sign-in">SIGN IN</div>
<nav class="nav">
  <span class="active" style="left:539px">HOME</span>
  <span style="left:606px">HOW IT WORKS</span>
  <span style="left:735px">PRICING</span>
  <span style="left:825px">ABOUT US</span>
  <span style="left:922px">BLOG</span>
  <span style="left:989px">CONTACT US</span>
</nav>
<h1 class="abs hero-title heading"><span>BETTER BIKES FOR</span><b>THE BETTER JOURNEY</b></h1>
<div class="abs check-box"></div>
<svg class="abs" style="left:150px;top:342px" width="14" height="14" viewBox="0 0 14 14"><rect x="1.5" y="2.5" width="11" height="10" fill="none" stroke="#1a1a1a" stroke-width="1.4"/><line x1="1.5" y1="5.5" x2="12.5" y2="5.5" stroke="#1a1a1a" stroke-width="1.4"/><line x1="4" y1="1" x2="4" y2="3.5" stroke="#1a1a1a" stroke-width="1.4"/><line x1="10" y1="1" x2="10" y2="3.5" stroke="#1a1a1a" stroke-width="1.4"/></svg>
<div class="abs check-label">CHECK AVAILABILITY</div>
<div class="btn check-btn">CHECK</div>
<div class="dot" style="left:557px"></div>
<div class="dot" style="left:576px"></div>
<div class="dot on" style="left:595px"></div>
<div class="dot" style="left:617px"></div>
<div class="dot" style="left:636px"></div>

<!-- pricing -->
<h2 class="section-title" style="top:702px">PRICING</h2>
<div class="rule" style="left:579px;top:750px"></div>
<div class="price-card" style="left:157px">
  <div class="price">$2.<sup>00</sup></div>
  <div class="plan">Single Ride</div>
  <p class="price-text">Lorem ipsum dolor sit amet consectetur adipiscing elit sed do eiusmod tempor incididunt ut labore et dolore.</p>
  <div class="btn">PAY ONLINE</div>
</div>
<div class="price-card" style="left:460px">
  <div class="price">$6.<sup>00</sup></div>
  <div class="plan">Day Pass</div>
  <p class="price-text">Lorem ipsum dolor sit amet consectetur adipiscing elit sed do eiusmod tempor incididunt ut labore et dolore.</p>
  <div class="btn">PAY ONLINE</div>
</div>
<div class="price-card" style="left:762px">
  <div class="price">$75.<sup>00</sup></div>
  <div class="plan">Annual Membership</div>
  <p class="price-text">Lorem ipsum dolor sit amet consectetur adipiscing elit sed do eiusmod tempor incididunt ut labore et dolore.</p>
  <div class="btn">PAY ONLINE</div>
</div>

<!-- welcome -->
<div class="welcome-photo" role="img" aria-label="Woman with a backpack standing with her bicycle on a boardwalk beside a green-hilled lake"></div>
<div class="abs welcome-panel"></div>
<div class="abs welcome-kicker">Welcome to</div>
<div class="abs welcome-name">Tall Fern Bicycle Rental</div>
<div class="rule" style="left:195px;top:1322px;width:44px;height:3px"></div>
<p class="abs welcome-text">On the other hand, we denounce with righteous indignation and dislike men who are so beguiled and demoralized by the charms of pleasure of the moment, so blinded by desire, that they cannot foresee the pain and trouble that are bound to ensue; and equal blame belongs to those who fail in their duty through weakness of will, which is the sam.</p>
<div class="btn" style="left:195px;top:1570px;width:102px;height:30px">READ MORE</div>

<!-- how it works -->
<h2 class="section-title" style="top:1736px">HOW IT WORKS</h2>
<div class="rule" style="left:579px;top:1787px"></div>
<div class="step-photo" style="left:132px;background:linear-gradient(135deg,#e6e6e6,#9a9a9a 60%,#5a5a5a)" role="img" aria-label="Two mechanics adjusting a white bicycle in a bike shop"></div>
<div class="step-photo" style="left:452px;background:linear-gradient(180deg,#dfe6ec 0%,#c6ccd2 55%,#8d8178 100%)" role="img" aria-label="Cyclist riding along a waterfront promenade"></div>
<div class="step-photo" style="left:774px;background:linear-gradient(90deg,#7fa8d6,#a9c3e3 50%,#8fb3dc)" role="img" aria-label="Two parked bicycles against a pale blue wall"></div>
<div class="step-title" style="left:132px">1. Unlock</div>
<div class="step-title" style="left:452px">2. Ride</div>
<div class="step-title" style="left:774px">3. Return</div>
<p class="step-text" style="left:132px">On the other hand, we denounce with righteous indignation and dislike men who are so beguiled and demoralized by the charms of pleasure</p>
<p class="step-text" style="left:452px">On the other hand, we denounce with righteous indignation and dislike men who are so beguiled and demoralized by the charms of pleasure</p>
<p class="step-text" style="left:774px">On the other hand, we denounce with righteous indignation and dislike men who are so beguiled and demoralized by the charms of pleasure</p>

<!-- fat tire -->
<div class="fat-photo" role="img" aria-label="Smiling woman riding a fat tire bicycle down a tree-lined path in spring"></div>
<h2 class="abs fat-title">WE RENT FAT TIRE<br>VORN BICYCLES.</h2>
<div class="rule" style="left:164px;top:2420px;width:44px"></div>
<p class="abs fat-text">At vero eos et accusamus et iusto odio digni ssimos ducimus qui blanditiis praesentium voluptatum deleniti atque corrupti quos dolores et quas molestias excepturi sint occaecati cupiditate non provident, similique.</p>
<div class="btn" style="left:167px;top:2623px;width:101px;height:29px">READ MORE</div>

<!-- testimonials -->
<div class="testi-band"></div>
<h2 class="section-title" style="top:2803px;color:var(--white)">TESTIMONIALS</h2>
<div class="rule" style="left:579px;top:2855px;background:var(--white)"></div>
<svg class="abs" style="left:74px;top:3034px" width="18" height="26" viewBox="0 0 18 26"><polyline points="14,3 4,13 14,23" fill="none" stroke="#fff" stroke-width="3"/></svg>
<svg class="abs" style="left:1114px;top:3034px" width="18" height="26" viewBox="0 0 18 26"><polyline points="4,3 14,13 4,23" fill="none" stroke="#fff" stroke-width="3"/></svg>
<div class="testi-card" style="left:132px">
  <div class="quote">“</div><div class="stars">★★★★★</div>
  <p class="testi-text">Lorem ipsum dolor sit amet, con sect etur adipiscing elit, sed do eiusmod tempor incididunt ut labore et dolore magna aliqua. Ut enim ad minim veniam, quis nostrud exercitation ullamco laboris nisi ut aliquip ex ea commodo consequat.</p>
  <div class="testi-rule"></div><div class="testi-name">MARLON</div>
</div>
<div class="testi-card" style="left:450px">
  <div class="quote">“</div><div class="stars">★★★★★</div>
  <p class="testi-text">Lorem ipsum dolor sit amet, con sect etur adipiscing elit, sed do eiusmod tempor incididunt ut labore et dolore magna aliqua. Ut enim ad minim veniam, quis nostrud exercitation ullamco laboris nisi ut aliquip ex ea commodo consequat.</p>
  <div class="testi-rule"></div><div class="testi-name">MARLON</div>
</div>
<div class="testi-card" style="left:771px">
  <div class="quote">“</div><div class="stars">★★★★★</div>
  <p class="testi-text">Lorem ipsum dolor sit amet, con sect etur adipiscing elit, sed do eiusmod tempor incididunt ut labore et dolore magna aliqua. Ut enim ad minim veniam, quis nostrud exercitation ullamco laboris nisi ut aliquip ex ea commodo consequat.</p>
  <div class="testi-rule"></div><div class="testi-name">MARLON</div>
</div>

<!-- footer -->
<footer class="footer"></footer>
<div class="abs foot-dot"></div>
<div class="abs foot-brand">Tall Fern Bicycle Rental</div>

<div class="foot-head" style="left:446px">MENU</div>
<div class="abs foot-menu">HOME<br>HOW IT WORKS<br>PRICING<br>ABOUT US<br>BLOG<br>CONTACT US</div>

<div class="foot-head" style="left:653px">CONTACT US</div>
<div class="foot-icon" style="left:650px;top:3363px"><svg width="28" height="28" viewBox="0 0 28 28"><path d="M14 7a5 5 0 0 0-5 5c0 4 5 9 5 9s5-5 5-9a5 5 0 0 0-5-5z" fill="#2a2a2a"/><circle cx="14" cy="12" r="1.8" fill="#fff"/></svg></div>
<div class="foot-line" style="left:690px;top:3358px">2150 Alder Ridge Road<br>Pinecrest, CA 95364</div>
<div class="foot-icon" style="left:650px;top:3425px"><svg width="28" height="28" viewBox="0 0 28 28"><path d="M10 8c1 0 2 2.5 2 3s-1 1-1 1.5c0 1 3 4 4 4 .5 0 1-1 1.5-1s3 1 3 2-1 2.5-2.5 2.5C12 20 8 16 8 10.5 8 9 9 8 10 8z" fill="#2a2a2a"/></svg></div>
<div class="foot-line" style="left:690px;top:3420px">Call Us<br>888.888.8888</div>
<div class="foot-icon" style="left:650px;top:3487px"><svg width="28" height="28" viewBox="0 0 28 28"><rect x="8" y="9.5" width="12" height="9" fill="#2a2a2a"/><polyline points="8,10 14,15 20,10" fill="none" stroke="#fff" stroke-width="1.3"/></svg></div>
<div class="foot-line" style="left:690px;top:3482px">E mail Us<br>info@tallfernbicyclerental.com</div>

<div class="foot-head" style="left:938px">FOLLOW US</div>
<div class="foot-icon" style="left:938px;top:3363px"></div>
<div class="foot-line" style="left:980px;top:3358px">Like us on<br>OUR PAGE</div>
<div class="foot-icon" style="left:938px;top:3425px"></div>
<div class="foot-line" style="left:980px;top:3420px">Follow us on<br>OUR FEED</div>
<div class="foot-icon" style="left:938px;top:3487px"></div>
<div class="foot-line" style="left:980px;top:3482px">Follow us on<br>OUR NETWORK</div>

<div class="abs foot-rule"></div>
<div class="abs copyright">Copyright © 2020 All Rights Reserved</div>

</body>
</html>
```